Investment Memorandum Document

IM for Harbourline Lending Fund - is the document that needs work

Make sure it is all done in MS WORD so that i or lawyers can edit some words if required

the IM is NOT final but its 95% of the way there. Maybe a few more pages and wording changes - but that is something i can do i guess or you can easier adjust

Just to typeset and pretty it all up - a few sample finished products have been uploaded for reference.

KTR IM is the one i like - but feel free to show off your skills

put 1.2 to 1.8 all in contrasting row tables

Target Market(s)

Individual and Institutional investors with money

Industry/Entity Type

Investment Banking

Colors

Designer to choose colors to be used in the design.

Requirements
Must have
• clear professional layout and easy on the eye
• https://www.filevaultexample.net/sh/84k3p77zrm2wqtn/BBDfpqWem3PvtsLxQZMUD41Lb?dl=0
• use the link above for high res images
Nice to have
• pictures and graphics
Should not have
• cartoons

```html
<!DOCTYPE html>
<html lang="en">
<head>
<meta charset="utf-8">
<title>Diversified Commercial Income Fund – Information Memorandum</title>
<link href="https://fonts.googleapis.com/css2?family=Open+Sans:wght@400;600;700&family=Cinzel:wght@500&display=swap" rel="stylesheet">
<style>
:root{
  --bg:#f4f5f7;
  --paper:#ffffff;
  --ink:#3a3d42;
  --muted:#8a8f96;
  --blue:#2a8bd0;
  --navy:#1d3c6b;
  --sky:#6fa6d8;
  --gold:#b18a45;
  --rule:#d9dde2;
  --row:#eef3f8;
}
*{box-sizing:border-box;margin:0;padding:0}
html,body{width:1200px;height:1200px;overflow:hidden;background:var(--bg)}
body{position:relative;font-family:"Open Sans",Arial,sans-serif;color:var(--ink)}
.spread,.single{position:absolute;display:flex;box-shadow:0 2px 6px rgba(0,0,0,.18)}
.page{position:relative;width:100%;height:100%;background:var(--paper);padding:16px 14px 18px;overflow:hidden}
.page.right{border-right:6px solid var(--gold)}
.page.left{box-shadow:inset -6px 0 8px -6px rgba(0,0,0,.12)}
.page p,.page li{font-size:4.2px;line-height:1.45;margin-bottom:3px;text-align:justify}
.page h2{font-size:8px;font-weight:400;color:var(--blue);margin-bottom:6px}
.page h3{font-size:4.6px;font-weight:700;color:var(--blue);text-transform:uppercase;margin:4px 0 2px}
.page h4{font-size:4.4px;font-weight:600;color:var(--blue);margin:4px 0 2px}
.page ul{padding-left:8px;margin-bottom:3px}
.folio{position:absolute;bottom:7px;right:14px;font-size:3.4px;color:var(--muted)}
.photo{background:linear-gradient(160deg,#dfe9f4 0%,var(--sky) 40%,var(--navy) 100%)}
.brand{display:flex;align-items:center;gap:5px;font-family:"Open Sans",sans-serif;font-weight:600;letter-spacing:2px}
.brand i{display:block;width:9px;height:9px;background:var(--gold)}
/* cover */
.cover{padding:0}
.cover .photo{position:absolute;inset:0}
.cover .brand{position:absolute;top:44px;left:36px;color:#fff;font-size:15px}
.cover .title{position:absolute;top:98px;left:30px;color:#fff;font-size:7.6px;font-weight:600;line-height:1.35}
.cover .roles{position:absolute;right:20px;bottom:26px;text-align:right;color:#fff}
.cover .roles b{display:block;font-size:7px;font-weight:600;margin-top:6px}
.cover .roles span{display:block;font-size:5.4px}
/* toc */
.toc h2{font-size:5.6px;font-weight:700;text-decoration:underline;margin:26px 0 8px}
.toc-row{display:flex;justify-content:space-between;font-size:4.6px;border-bottom:1px dotted var(--rule);padding:2px 0}
.toc-row em{font-style:normal;width:12px;display:inline-block}
/* key features table */
.kf{width:100%;border-collapse:collapse}
.kf td{font-size:3.9px;line-height:1.4;vertical-align:top;padding:3px 2px;border-top:1px solid var(--rule)}
.kf tr:nth-child(odd) td{background:var(--row)}
.kf td:first-child{width:34px;font-weight:700}
/* flow chart */
.flow{width:100%;height:92px;margin:4px 0 6px}
.callout{border:1px solid var(--blue);color:var(--blue);font-size:4.3px;text-align:center;padding:6px 10px;margin:8px 12px}
</style>
</head>
<body>

<!-- Row 1 -->
<div class="single" style="left:30px;top:60px;width:232px;height:328px">
  <div class="page cover">
    <div class="photo" role="img" aria-label="Upward view of glass office towers in blue tones"></div>
    <div class="brand"><i></i>CORVANE</div>
    <div class="title">Diversified Commercial Income Fund<br>Information Memorandum</div>
    <div class="roles">
      <b>Investment Manager</b><span>Corvane Asset Management Pty Ltd</span>
      <b>Trustee</b><span>Northgate Investments and Lending Corporation Pty Ltd</span>
    </div>
  </div>
</div>

<div class="spread" style="left:272px;top:60px;width:448px;height:328px">
  <div class="page left" style="padding:0">
    <div class="photo" style="position:absolute;inset:0;clip-path:polygon(0 0,100% 0,100% 100%,0 58%)" role="img" aria-label="Skyscrapers seen from below against a pale sky"></div>
    <div class="photo" style="position:absolute;inset:0;clip-path:polygon(0 64%,100% 100%,0 100%);opacity:.85" role="img" aria-label="Tower facade detail"></div>
  </div>
  <div class="page right toc">
    <h2>TABLE OF CONTENT</h2>
    <div class="toc-row"><span>Message from the Managing Director</span><span>5</span></div>
    <div class="toc-row"><span><em>1.</em>The Fund</span><span>6</span></div>
    <div class="toc-row"><span><em>2.</em>The loan Investments</span><span>11</span></div>
    <div class="toc-row"><span><em>3.</em>Risks</span><span>13</span></div>
    <div class="toc-row"><span><em>4.</em>Fees and costs</span><span>17</span></div>
    <div class="toc-row"><span><em>5.</em>Meridian Crest Investment Group</span><span>18</span></div>
    <div class="toc-row"><span><em>6.</em>Management of the Fund</span><span>19</span></div>
    <div class="toc-row"><span><em>7.</em>Taxation information</span><span>20</span></div>
    <div class="toc-row"><span><em>8.</em>Additional Information</span><span>21</span></div>
    <div class="toc-row"><span><em>9.</em>Application Process</span><span>24</span></div>
    <div class="toc-row"><span><em>10.</em>Glossary</span><span>25</span></div>
    <div class="toc-row"><span><em>11.</em>Corporate Directory</span><span>27</span></div>
  </div>
</div>

<div class="spread" style="left:728px;top:60px;width:448px;height:328px">
  <div class="page left">
    <h3>Notice</h3>
    <p>This information memorandum is dated and is issued by Northgate Investments and Lending Corporation Pty Ltd as trustee of the Diversified Commercial Income Fund. The Trustee has appointed Corvane Asset Management Pty Ltd as the investment manager of the Fund under the Investment Management Agreement.</p>
    <p>The purpose of this IM is to provide information for prospective Investors to decide whether they wish to invest in the Fund. The Fund's trust deed provides for different Classes of Units, and Units of each Class have different rights and obligations.</p>
    <h3>No disclosure required</h3>
    <p>This IM is intended to provide potential Investors with information only and does not constitute a product disclosure statement or other disclosure document required by the Corporations Act. This IM has not been lodged with the Australian Securities and Investments Commission.</p>
    <h3>Restrictions on distribution</h3>
    <p>This IM does not constitute, and may not be used for the purposes of, an offer of Units or an invitation to apply to participate in the Fund by any person in any jurisdiction in which such offer or invitation is not authorised.</p>
    <p>No action has been taken to register or qualify interests in the Fund, the invitation to participate in the Fund, or to otherwise permit any public offering of Fund interests in any jurisdiction other than Australia. It is the responsibility of prospective Investors to satisfy themselves as to full compliance with the relevant laws.</p>
    <p>By receiving and viewing this IM, the recipient is warranting that they are legally entitled to do so and that they are a qualifying wholesale client under the Corporations Act.</p>
    <h3>No responsibility for contents of document</h3>
    <p>To the maximum extent permitted by law, none of the Trustee, the Investment Manager, or any of their associated entities, directors or officers, makes any representation as to the accuracy of the information contained in this IM.</p>
    <p>This IM must be read in conjunction with the Fund's Trust Deed which is available free of charge by contacting the Trustee.</p>
    <div class="folio">Corvane AM Diversified Commercial Income Fund – Information Memorandum | 3</div>
  </div>
  <div class="page right">
    <h3>No distribution</h3>
    <p>Distribution of this IM to any person other than the persons receiving a copy of this IM from the Trustee or the Investment Manager is unauthorised. Any photocopying, disclosure or alteration of the contents of this IM is prohibited.</p>
    <h3>Not regulated by APRA</h3>
    <p>The Trustee is not authorised under the Banking Act and is not supervised by APRA, and investments in the Fund are not covered by the deposit or protection provisions available to depositors.</p>
    <h3>Forward-looking statements</h3>
    <p>This IM includes forward looking statements that may contain words such as believe, intend, estimate, expect and words of similar meaning. All statements other than statements of historical facts included in this IM are forward looking statements. Such statements involve known and unknown risks, uncertainties and other important factors that could cause actual results to differ materially.</p>
    <p>Any forward looking statements are based on numerous assumptions regarding a Project, the present and future business, investment strategies and the markets in which a Project will operate in the future.</p>
    <h3>Independent advice recommended</h3>
    <p>Prospective Investors should not construe the contents of this IM as tax, legal or investment advice. The information contained in this IM is general information only and does not take into account your objectives, financial situation or needs. You should seek appropriate professional advice.</p>
    <h3>No guarantee</h3>
    <p>An investment in the Fund is subject to investment risk, including the loss of income and capital invested. None of the Trustee, the Investment Manager or any of their directors guarantees the return of capital.</p>
    <h3>Trustee limitation of liability</h3>
    <p>Except in certain circumstances, the Trustee enters into transactions for the Fund in its capacity as trustee of the Fund only, not in its own capacity.</p>
    <h3>Updated information</h3>
    <p>The information contained in this IM may change and the IM may be updated or replaced from time to time.</p>
    <h3>Confidentiality</h3>
    <p>This IM is confidential and is provided to prospective Investors for them to consider investing in the Fund.</p>
    <h3>Glossary</h3>
    <p>Certain capitalised words and expressions used in this IM are defined in the Glossary. All amounts are in Australian Dollars.</p>
    <div class="folio">Corvane AM Diversified Commercial Income Fund – Information Memorandum | 4</div>
  </div>
</div>

<!-- Row 2 -->
<div class="spread" style="left:145px;top:450px;width:446px;height:325px">
  <div class="page left" style="padding-top:30px">
    <h2>Message from the Managing Director</h2>
    <p>Dear investor,</p>
    <p>On behalf of Corvane Asset Management it is my pleasure to invite you to participate in our flagship Diversified Commercial Income Fund.</p>
    <p>It is supported by a dedicated and experienced team of investment and property professionals, providing wholesale clients access to exclusive opportunities whilst delivering attractive risk-adjusted returns.</p>
    <p>At the core of Corvane's business are the same disciplines, due diligence and values which you afford to your own money. This approach has elevated us to trusted partner level with our strategic partners and clients alike.</p>
    <p>We are proud to partner with Meridian Crest Investment Group in our flagship fund. Since 2012, MCIG has made headlines with its innovative approach and successful delivery of unique assets that have changed the city landscape.</p>
    <p>Its strong balance sheet and respect-based approach has seen the likes of global brands such as hotel and retail operators choose MCIG as preferred partner.</p>
    <p>The Fund is a managed investment scheme and established as a unit trust. Investment in the Fund is available to a limited number of Wholesale Clients on an invitation only basis.</p>
    <p>The key benefits of investing in the Fund include:</p>
    <ul>
      <li>Attractive fixed income distributions</li>
      <li>Exposure to a significant high-end commercial development being undertaken by MCIG</li>
      <li>The ability to begin or continue your investment relationship with us</li>
      <li>All fees absorbed by the Investment Manager</li>
    </ul>
    <p>As with any investment, there are risks associated with an investment in the Fund and I encourage you to read the IM thoroughly before deciding to invest.</p>
    <p>Yours sincerely,</p>
    <p style="margin-top:8px">Daniel Arlow<br>Managing Director</p>
    <div class="folio">5</div>
  </div>
  <div class="page right">
    <h2>1. The Fund</h2>
    <h4>1.1 Fund Outline</h4>
    <p>The Fund is an unregistered managed investment scheme which pools Investors' monies and invests in loans predominantly used for property investment and development projects in Australia. The Trustee has appointed the Investment Manager of the Fund.</p>
    <svg class="flow" viewBox="0 0 190 92" aria-label="Fund structure diagram">
      <g font-family="Open Sans" font-size="3.4" text-anchor="middle" fill="#fff">
        <rect x="78" y="2" width="34" height="12" fill="#9aa3ad"/><text x="95" y="9.5">Qualifying Investors</text>
        <rect x="2" y="32" width="44" height="14" fill="#1d3c6b"/><text x="24" y="40.5">Investment Manager</text>
        <rect x="72" y="32" width="46" height="14" fill="#6aa84f"/><text x="95" y="40.5">Diversified Commercial Fund</text>
        <rect x="144" y="28" width="44" height="10" fill="#1d3c6b"/><text x="166" y="34.5">Wholesale Trustee</text>
        <rect x="144" y="40" width="44" height="10" fill="#7a8590"/><text x="166" y="46.5">Administrator</text>
        <rect x="8" y="74" width="40" height="11" fill="#9fb8d2"/><text x="28" y="81">Cash Units</text>
        <rect x="75" y="74" width="40" height="11" fill="#9fb8d2"/><text x="95" y="81">Class 1 Loan Units</text>
        <rect x="142" y="74" width="40" height="11" fill="#9fb8d2"/><text x="162" y="81">Class 2 Loan Units</text>
      </g>
      <g stroke="#8a8f96" stroke-width=".5" fill="none">
        <path d="M95 14V32M46 39H72M118 39H144M95 46V62M28 62H162M28 62V74M95 62V74M162 62V74"/>
      </g>
    </svg>
    <p>The Fund will invest predominantly in loans used in connection with development projects managed or developed by Meridian Crest Investment Group.</p>
    <p>The Fund is structured to allow Qualifying Investors to acquire interests in Cash Units and Loan Units, each referable to a separate portfolio of assets.</p>
    <h4>Key Benefits of investing in the Fund</h4>
    <ul>
      <li>The Fund has an independent trustee that will provide an enhanced level of oversight ensuring loans are made in accordance with this IM.</li>
      <li>The underlying Projects are undertaken and managed by a property investment group with extensive experience.</li>
      <li>Transparency through regular investment reports provided by the Trustee.</li>
      <li>Accounting, financial reporting and tax affairs of the Fund managed by the Trustee.</li>
      <li>Audited by Pellman Audit Partners</li>
    </ul>
    <div class="folio">6</div>
  </div>
</div>

<div class="spread" style="left:600px;top:450px;width:446px;height:325px">
  <div class="page left">
    <h4>1.2 Fund Units</h4>
    <p>The Fund comprises of multiple classes of Units which includes Specified Loan Units and Loan Units. The following classes of Units are issued pursuant to this IM:</p>
    <p><b>Cash Units</b><br>Cash Units will comprise Basic Deposit Products only and will include cash management accounts and term deposits.</p>
    <p><b>Class 1 Loan Units and Class 2 Loan Units</b><br>Loan Units will comprise a portfolio of loan investments which includes senior debt loans, junior debt loans and unsecured loans. While the Investment Manager's intention is to have all available funds invested in loans, when they are not, they will be invested in Basic Deposit Products.</p>
    <p>The Trustee may, at its discretion, issue other classes of Units.</p>
    <h4>Issue of Units</h4>
    <p>Cash Units will be issued monthly within 5 Business Days after the end of the month in which the application for Cash Units is received and accepted by the Trustee.</p>
    <p>Class 1 Loan Units and Class 2 Loan Units will be issued monthly within 5 Business Days after the end of the month in which the application is received and accepted.</p>
    <h4>Unit Price</h4>
    <p>It is intended that Units will be issued at $1.00, however the Unit price is based on the underlying value of the Fund's assets referable to the particular class of Units.</p>
    <p>The withdrawal price for a Unit is also based on the underlying value of the Fund's assets. This price may be different from the price originally paid for the Unit.</p>
    <h4>1.3 Distributions</h4>
    <p>The rate and frequency of distributions will depend upon the class of Units held by the Investor.</p>
    <p><b>Cash Units</b><br>It is intended that distributions on Cash Units will be calculated and paid quarterly within 8 Business Days of the end of each calendar quarter.</p>
    <p>Investors will receive a proportion of the income referable to Cash Units based on the number of Cash Units they hold in relation to the total number of Cash Units on issue.</p>
    <p>Distributions may be paid and reinvested in Cash Units if the Investor makes an election in the Application Form.</p>
    <div class="folio">7</div>
  </div>
  <div class="page right">
    <h4>Loan Units</h4>
    <p>It is intended that distributions on Loan Units will be calculated and paid half yearly in arrears within 20 Business Days, however at the end of each financial year, due to the time required to prepare to complete tax compliance obligations, the Trustee will endeavour to pay final distributions once reporting is completed.</p>
    <p>Investors will receive a proportion of the income referable to Loan Units based on the number of Loan Units they hold and the number of days they held those Units during the quarter.</p>
    <p>Distributions may be paid and reinvested in Loan Units if the Investor makes an election.</p>
    <h4>1.4 Withdrawal rights</h4>
    <p>An Investor's ability to withdraw from the Fund will depend upon the class of Units held by the Investor.</p>
    <p>The withdrawal price for a Unit is also based on the underlying value of the assets referable to the particular class of Units.</p>
    <p><b>Cash Units</b><br>Generally, Cash Units may be withdrawn at any time by lodging a Withdrawal Request with the Trustee at least 5 Business Days prior to the end of a calendar month.</p>
    <p><b>Loan Units</b><br>Investments in Loan Units are not expected to be liquid.</p>
    <p><b>Class 1 Loan Units</b><br>Generally, Investors may not withdraw their Class 1 Loan Units within the first 12 months from the date of issue. Thereafter, withdrawals will be processed on a calendar quarterly basis with at least 45 Business Days' notice.</p>
    <p><b>Class 2 Loan Units</b><br>Generally, Investors may not withdraw their Class 2 Loan Units within the first 24 months from the date of issue. Thereafter, withdrawals will be processed on a calendar quarterly basis.</p>
    <h4>1.5 Transfer of Units</h4>
    <p>There will not be any established secondary market for the sale of Units, however an Investor may transfer the ownership of their Units at any time provided the transferee meets the requirements of an Investor.</p>
    <p>Under the Trust Deed, the Trustee has the discretion to refuse the transfer of Units and is not obliged to accept a transfer of Units.</p>
    <div class="folio">8</div>
  </div>
</div>

<!-- Row 3 -->
<div class="spread" style="left:24px;top:830px;width:436px;height:330px">
  <div class="page left">
    <h4>1.6 Borrowings</h4>
    <p>The Fund will not borrow for any purpose.</p>
    <h4>1.7 Other</h4>
    <p>The Fund will not enter into derivatives or foreign exchange contracts for any purpose.</p>
    <h4>1.8 Key Features</h4>
    <p>The table below is only a summary of the key features of an investment in the Fund. It is not intended to be exhaustive.</p>
    <table class="kf">
      <tr><td>Trustee</td><td>Northgate Investments and Lending Corporation Pty Ltd is the trustee of the Fund and will be responsible for holding title to the Fund's assets.</td></tr>
      <tr><td>Investment Manager</td><td>Corvane Asset Management Pty Ltd has been appointed as the investment manager of the Fund and is responsible for managing the Fund's assets. The Investment Manager will source and assess potential loans for the Fund.</td></tr>
      <tr><td>Administration Manager</td><td>NILC Funds Administration Pty Ltd is the Administration Manager of the Fund, responsible for processing applications and unit registry.</td></tr>
      <tr><td>Investment objective</td><td>The Investment Manager's aim is to provide Investors with attractive fixed income returns derived through investment in a portfolio of commercial loans made predominantly to special purpose vehicles, each responsible for undertaking a single project. Typically, Meridian Crest Investment Group will be the controlling shareholder of each SPV and will control the development project by way of a formal project management agreement.</td></tr>
      <tr><td>Who can invest in the Fund?</td><td>Investment in the Fund is only available to parties over 18 years of age, trusts or bodies corporate who, if residing in Australia, invest $500,000 or more in the Fund; or provide a certificate from a qualified accountant stating the Investor has net assets of at least $2.5 million or a gross income for each of the last two financial years of at least $250,000; or is a professional investor.</td></tr>
    </table>
    <div class="folio">9</div>
  </div>
  <div class="page right">
    <p style="margin-top:4px">For non-Australian residents, please contact the Trustee for information on qualifying criteria.</p>
    <table class="kf">
      <tr><td>Target Returns</td><td><b>Cash Units</b><br>The target return for Cash Units, before tax, after all fees, is the RBA Cash Rate.<br><b>Loan Units</b><br>The target return of each class of Loan Units are:<br>Class 1 Loan Units: 8% per annum (before tax, after all fees)<br>Class 2 Loan Units: 10% per annum (before tax, after all fees)<br>The Target Return is not guaranteed. The Fund may not be successful in meeting this objective.</td></tr>
      <tr><td>Minimum Initial Investment Amount</td><td><b>Cash Units</b><br>The minimum initial investment for Cash Units is $100,000 from a Qualifying Investor. Following the minimum initial investment, Investors may make further investments in increments of $20,000.<br><b>Loan Units</b><br>The minimum initial investment for Loan Units is $500,000 from a Qualifying Investor. Following the minimum initial investment, Investors may make further investments in increments of $50,000.<br>However, the Trustee may accept lower amounts from a Qualifying Investor in its absolute discretion.</td></tr>
    </table>
    <div class="folio">10</div>
  </div>
</div>

<div class="spread" style="left:488px;top:830px;width:448px;height:330px">
  <div class="page left">
    <h4>Market risk</h4>
    <p>This is the risk that negative market movements will affect the price of assets within a particular market. By their nature, markets experience periods of volatility involving price fluctuations of varying magnitudes. Property market risk is the risk that the property market as a whole declines in value.</p>
    <p>The Fund's assets will be made up of loans made for the purpose of property development. Therefore, factors which affect the property market may impact upon the value of Fund security.</p>
    <p>A fall in property values may affect the ability to fully recover the amount owing under a loan where a Borrower defaults. If the Borrower defaults and the security property is sold for less than the outstanding loan amount, this may result in the Fund suffering a loss.</p>
    <h4>Operational risk</h4>
    <p>Operational risk exists in all managed investments. This refers to the possibility the Investment Manager may fail to anticipate market movements or to manage the investment risks appropriately.</p>
    <p>There is also an inherent risk associated with the death or departure of the Trustee's or the Investment Manager's key personnel.</p>
    <h4>Regulatory and economic risk</h4>
    <p>There is the risk that the value of an investment may be affected by changes in domestic or international policies, regulations or laws, including taxation laws.</p>
    <h4>Investment risk</h4>
    <p>The investments identified and selected by the Manager for the Fund will not appreciate in value or may decrease in value in the case of a default by a Borrower.</p>
    <h4>Interest rate risk</h4>
    <p>Changes to interest rates can have a direct and indirect impact on the value of your security.</p>
    <h4>Credit risk</h4>
    <p>When investing in bank deposits and fixed interest securities it is necessary to consider credit risk.</p>
    <h4>Risks associated with the performance of the Investment Manager</h4>
    <p>The success of the Fund is dependent on the Investment Manager identifying suitable loans for the Fund and managing these loans to ensure that the loans are repaid.</p>
    <div class="folio">15</div>
  </div>
  <div class="page right">
    <p>This risk is mitigated by the fact that the loans must be made in accordance with the Lending Guidelines. The Trustee reviews the loans to ensure that they are made in accordance with the Lending Guidelines and this IM before it executes the loan documents.</p>
    <h4>Risks associated with the solvency and financial position of the Investment Manager and Borrowers</h4>
    <p>The financial performance of the loans will be impacted by the financial performance of the Investment Manager and the Borrowers, and the success of the Projects undertaken by these related entities.</p>
    <p>If the Investment Manager either becomes insolvent or encounters financial difficulties, which mean that it is unable to perform its role under the Investment Management Agreement, the Trustee will most likely need to terminate the agreement and appoint a replacement.</p>
    <p>This could result in you suffering a loss or a diminished return on your investment in the Fund.</p>
    <div class="callout">We strongly recommend that Investors obtain independent financial advice before investing in the Fund.</div>
    <div class="photo" style="position:absolute;left:0;right:0;bottom:18px;height:118px;background:linear-gradient(180deg,#dfe6ee,#b7a999 60%,#8c7f74)" role="img" aria-label="Modern high-rise commercial development building"></div>
    <div class="folio">16</div>
  </div>
</div>

<div class="single" style="left:952px;top:830px;width:226px;height:330px">
  <div class="page" style="display:flex;align-items:flex-end;justify-content:flex-end;padding:0 22px 34px 0">
    <div class="brand" style="color:var(--navy);font-size:7px"><i style="width:5px;height:5px"></i>CORVANE</div>
  </div>
</div>

</body>
</html>
```